tinyTally Resource Book - 10 maths tasks to do outside

I need a 22 (11 pages back to back) page A6 sized book produced to standard for submission to professional printer. Needs to be as .pdf file showing guide lines and allowances for colour bleed. I have text already written and submitted as attachment in a Word file with margins set to A6 size. The theme of the materials is "Nature Play" so using lots of pictures from nature (Australia preferably) and showing lots of patterns in nature (rocks, leaves, flower petals etc). Some of the tasks refer to specific activities, such as "shadows" and "floating" so would be great to illustrate appropriately. The big emphasis is on learning outside the classroom, getting kids to engage actively with nature. I would like to see the pages as full colour - so not white background. The book itself will be spiral bound along the top edge so a margin of at least 1cm will be required at the top of each page (or the bottom of even numbered pages). Book will be printed on plastic laminated matte paper for outdoor use. Font size needs to be big enough to read. Fonts sizes, alignments and page numbers are all different at the moment and need to be standardised. One photo is included in a page as a sample if you can use it, otherwise disregard. Logo for Wattlebrook Numeracy Guild is also included to have as part of the acknowledgements at the back of the book.

Target Market(s)

Book is for early childhood and preschool teachers.

Industry/Entity Type

Education

Font styles to use
Sans Serif

Requirements
Must have
• Colour and appeal.
Nice to have
• Use of natural colours instead of bright catchy colours but that is your call.
Should not have
• American spelling

```html
<!DOCTYPE html>
<html lang="en-AU">
<head>
<meta charset="utf-8">
<title>Same Same Different – tinyTally task card</title>
<link rel="stylesheet" href="https://fonts.googleapis.com/css2?family=Nunito:ital,wght@0,800;0,900;1,800;1,900&family=Questrial&display=swap">
<style>
  :root {
    --ink-navy: #2a2f8c;
    --ink-body: #1d1b16;
    --accent-red: #d0202a;
    --sand-light: #f3e9bd;
    --sand-mid: #e4d193;
    --sand-deep: #c9ad6e;
    --pebble: #b9a37a;
  }
  * { box-sizing: border-box; margin: 0; padding: 0; }
  html, body { width: 848px; height: 1200px; overflow: hidden; background: #fff; }
  .task-card {
    position: relative;
    width: 848px;
    height: 1200px;
    overflow: hidden;
    font-family: "Nunito", sans-serif;
    color: var(--ink-navy);
  }
  .nature-backdrop {
    position: absolute;
    inset: 0;
    background:
      radial-gradient(ellipse 260px 420px at 640px 980px, rgba(185,163,122,0.75), rgba(185,163,122,0) 70%),
      radial-gradient(ellipse 520px 260px at 330px 880px, rgba(150,130,90,0.35), rgba(150,130,90,0) 70%),
      linear-gradient(180deg, var(--sand-light) 0%, var(--sand-mid) 55%, var(--sand-deep) 100%);
  }
  .task-title {
    position: absolute;
    top: 30px; left: 0; right: 0;
    text-align: center;
    font-weight: 900;
    font-size: 50px;
    line-height: 64px;
  }
  .outcome-heading {
    position: absolute;
    top: 112px; left: 50px; right: 50px;
    text-align: center;
    font-weight: 900;
    font-size: 34px;
    line-height: 45px;
  }
  .prompt {
    position: absolute;
    left: 58px; right: 40px;
    font-weight: 900;
    font-style: italic;
    font-size: 30px;
    line-height: 39px;
  }
  .prompt--children { top: 290px; }
  .prompt--educators { top: 524px; }
  .prompt--task { top: 818px; }
  .statement {
    position: absolute;
    left: 138px; right: 48px;
    font-family: "Questrial", sans-serif;
    color: var(--ink-body);
    font-size: 37px;
    line-height: 49px;
    hyphens: manual;
  }
  .statement--children { top: 376px; }
  .statement--educators { top: 608px; }
  .opportunity-list {
    position: absolute;
    top: 862px; left: 74px; right: 60px;
    list-style: none;
    font-family: "Questrial", sans-serif;
    color: var(--ink-body);
    font-size: 28px;
    line-height: 38px;
  }
  .opportunity-list li {
    position: relative;
    padding-left: 32px;
    margin-bottom: 2px;
  }
  .opportunity-list li::before {
    content: "";
    position: absolute;
    left: 2px; top: 11px;
    width: 15px; height: 15px;
    background: var(--accent-red);
    transform: rotate(45deg);
  }
</style>
</head>
<body>
  <main class="task-card">
    <div class="nature-backdrop" role="img" aria-label="Photograph of smooth pebbles stacked on soft sand with a leaf in the background"></div>

    <h1 class="task-title">3. Same Same Different</h1>

    <h2 class="outcome-heading">EYLF – Outcome 2: Children are con-<br>nected with and contribute to their<br>world</h2>

    <p class="prompt prompt--children">Children respond to diversity with respect<br>when they...</p>
    <p class="statement statement--children">notice and react in positive ways to similarities and differences among people</p>

    <p class="prompt prompt--educators">Educators promote this learning when<br>they...</p>
    <p class="statement statement--educators">plan experiences and provide re-<br>sources that broaden children’s perspectives and encourage ap-<br>preciation of diversity</p>

    <p class="prompt prompt--task">This task provides an opportunity to:</p>
    <ul class="opportunity-list">
      <li>explore the concepts of “same” and “different”</li>
      <li>discuss diversity</li>
      <li>model and sort based on specific crite-<br>ria</li>
      <li>celebrate similarities and differences</li>
    </ul>
  </main>
</body>
</html>
```